Timber Crest Construction Needs business card

Hey we are in need of business card designs. I have upload our logo as a guideline, but free feel to run with it or come up with something unique.
Pls have fun with it and be creative. the name says it all!
i will give some directions after i see a few entries..
Updates
Logo source file has been uploaded..
Hey because of the logo is so colourful already.
Can we have a few submissions with less colour.
Also we are looking for clever/hidden/descriptive business card.

```html
<!DOCTYPE html>
<html lang="en">
<head>
<meta charset="utf-8">
<title>Timber Crest Construction – Business Card</title>
<link rel="stylesheet" href="https://fonts.googleapis.com/css2?family=Roboto+Condensed:wght@400;700&family=Roboto:wght@400;500&display=swap">
<style>
  :root {
    --green: #0f9444;
    --blue: #1a82cc;
    --blue-dark: #0d72bd;
    --white: #ffffff;
    --paper: #f1f1f1;
    --grey-text: #6f6f6f;
    --ink: #3a3a3a;
    --backdrop: #d9d9d9;
  }
  * { margin: 0; padding: 0; box-sizing: border-box; }
  html, body { width: 1200px; height: 903px; overflow: hidden; }
  body {
    background: var(--backdrop);
    position: relative;
    font-family: "Roboto", Arial, sans-serif;
  }
  .card {
    position: absolute;
    width: 700px;
    height: 400px;
    overflow: hidden;
    background: var(--white);
    box-shadow: 0 6px 18px rgba(0,0,0,0.25);
  }
  .card--back { left: 60px; top: 40px; }
  .card--front { left: 440px; top: 470px; background: linear-gradient(180deg, var(--paper), var(--white)); }

  .band { position: absolute; left: 0; width: 100%; }
  .band--green { background: var(--green); }
  .band--blue { background: var(--blue); }

  .brand {
    position: absolute;
    display: flex;
    align-items: center;
    gap: 12px;
    color: var(--grey-text);
    font-family: "Roboto Condensed", Arial, sans-serif;
    font-weight: 700;
    text-transform: uppercase;
    letter-spacing: 0.5px;
    white-space: nowrap;
  }
  .brand__mark { background: var(--blue); display: block; }
  .card--back .brand { left: 50%; top: 190px; transform: translateX(-50%); font-size: 34px; }
  .card--back .brand__mark { width: 34px; height: 34px; }
  .card--front .brand { left: 40px; top: 195px; font-size: 24px; }
  .card--front .brand__mark { width: 26px; height: 26px; }

  .address {
    position: absolute;
    right: 40px;
    top: 48px;
    text-align: right;
    color: var(--ink);
    font-size: 17px;
    line-height: 1.45;
    letter-spacing: 1px;
  }

  .name-block {
    position: absolute;
    left: 0; top: 262px;
    width: 420px; height: 118px;
    background: var(--blue-dark);
    padding: 26px 0 0 90px;
    color: var(--white);
  }
  .name-block__name {
    font-family: "Roboto Condensed", Arial, sans-serif;
    font-weight: 700;
    font-size: 36px;
    letter-spacing: 1px;
    line-height: 1;
  }
  .name-block__role {
    font-size: 14px;
    letter-spacing: 1.5px;
    margin-top: 6px;
  }

  .contact-panel {
    position: absolute;
    left: 420px; top: 168px;
    width: 280px; height: 212px;
    background: var(--green);
  }
  .contact-box {
    position: absolute;
    left: 20px; top: 20px;
    width: 244px; height: 140px;
    background: var(--blue);
    padding: 16px 14px 0 0;
    list-style: none;
    color: var(--white);
    font-size: 11.5px;
    letter-spacing: 0.5px;
  }
  .contact-box li {
    display: flex;
    justify-content: flex-end;
    align-items: center;
    gap: 8px;
    height: 27px;
  }
  .icon {
    width: 16px; height: 16px;
    background: var(--white);
    border-radius: 2px;
    display: flex; align-items: center; justify-content: center;
  }
  .icon svg { width: 11px; height: 11px; fill: var(--blue); }
</style>
</head>
<body>

  <section class="card card--back" aria-label="Business card back">
    <div class="band band--green" style="top:0;height:100px"></div>
    <div class="band band--blue" style="top:100px;height:20px"></div>
    <div class="band band--blue" style="top:278px;height:20px"></div>
    <div class="band band--green" style="top:298px;height:102px"></div>
    <div class="brand"><span class="brand__mark"></span>Timber Crest Construction</div>
  </section>

  <section class="card card--front" aria-label="Business card front">
    <address class="address" style="font-style:normal">
      42 Harlow Road,<br>3rd Mill Street W.
    </address>
    <div class="band band--blue" style="top:150px;height:18px"></div>
    <div class="brand"><span class="brand__mark"></span>Timber Crest Construction</div>

    <div class="name-block">
      <div class="name-block__name">DANIEL HALE</div>
      <div class="name-block__role">GENERAL MANAGER</div>
    </div>

    <div class="contact-panel">
      <ul class="contact-box">
        <li>014 527 3390
          <span class="icon"><svg viewBox="0 0 24 24"><path d="M6.6 10.8a15 15 0 0 0 6.6 6.6l2.2-2.2c.3-.3.7-.4 1-.2 1.1.4 2.3.6 3.6.6.6 0 1 .4 1 1V20c0 .6-.4 1-1 1A17 17 0 0 1 3 4c0-.6.4-1 1-1h3.5c.6 0 1 .4 1 1 0 1.3.2 2.5.6 3.6.1.3 0 .7-.2 1z"/></svg></span>
        </li>
        <li>014 527 3391
          <span class="icon"><svg viewBox="0 0 24 24"><path d="M5 3h14v18H5z M8 6v3h8V6z M8 12v2h2v-2z M11 12v2h2v-2z M14 12v2h2v-2z M8 16v2h2v-2z M11 16v2h2v-2z M14 16v2h2v-2z"/></svg></span>
        </li>
        <li>office@timbercrest.com
          <span class="icon"><svg viewBox="0 0 24 24"><path d="M2 5h20v14H2z M4 7v.5l8 5 8-5V7l-8 5z" fill-rule="evenodd"/></svg></span>
        </li>
        <li>www.timbercrest.com
          <span class="icon"><svg viewBox="0 0 24 24"><circle cx="12" cy="12" r="9"/></svg></span>
        </li>
      </ul>
    </div>
  </section>

</body>
</html>
```